Design a clean homepage for a travel portal based in the US catering to Asians. The design should be able to be used on other pages, or color scheme menu layout, header and footer should be usable on other pages.

Include the main options for users to click, as an example some could be; 1. Local Tour Company 2. Local Tour Guide 3. Transportation Company 4. Tour Packages

Think like www.craftmingle.net who brings designers and clients together we are bringing Tour company, Tour guide, Bus/Transportation company directly to those who need it. This is for a two way portal, not a common one way portal like regular booking sites.

Assume that a person arrives or is planning on arriving at a destination, what are some options that should be on the page, layout of the options: squares, rectangles, stars, scroll slides, whatever makes you feel fun, elegant, fresh, uplifting.

Feelings we want to convey: fun, elegant, fresh, uplifting, interesting, energetic

Update:
When we said this should be a simple design, we meant simple for the end user to understand what was going on. I have attached a screenshot of a website, that it is very easy to understand what its purpose is.

How you decide to set up picture/scenery areas, logo area, menu area, where the options go is all up to you. Would like it to be clean and inviting, we would also like the options to be colors that call the users to action(make them click). This doesn't have to be colors so much as design. If you have further questions feel free to message me.

Attached is our logo in various styles for you to choose from.

Target Market(s)

Travel, package tours, international students, business trips

Industry/Entity Type

Travel Industry

Number of Pages Required

1 page

Colors
ec1f27
ffffff
0255a3
474747
7f7f7f
5c5c5c
aaaaaa

Requirements
Must have
• 1. Local Tour Company 2. Local Tour Guide 3. Transportation Company 4. Tour Packages
Should not have
• Our main goal is not to sell flights or hotel rooms, so this can be an element on the page(or not) but it should not be very central/obvious.

```html
<!DOCTYPE html>
<html lang="en">
<head>
<meta charset="utf-8">
<title>Westbound Trails — Travel Portal</title>
<link href="https://fonts.googleapis.com/css2?family=Open+Sans:wght@400;600;700&display=swap" rel="stylesheet">
<style>
:root{
  --red:#ec1f27;
  --blue:#0255a3;
  --blue-dark:#01417d;
  --blue-deep:#013566;
  --white:#ffffff;
  --ink:#474747;
  --grey:#7f7f7f;
  --grey-mid:#5c5c5c;
  --grey-light:#aaaaaa;
  --line:#e3e3e3;
  --panel:#f2f2f2;
  --night:#1d2733;
}
*{box-sizing:border-box;margin:0;padding:0}
html,body{width:1200px;height:2900px;overflow:hidden}
body{font-family:"Open Sans",Arial,sans-serif;color:var(--ink);background:var(--white);font-size:14px;line-height:1.5}
.wrap{width:1040px;margin:0 auto;position:relative}

/* header */
.site-header{height:112px;background:var(--white)}
.site-header .wrap{height:112px;display:flex;align-items:center;justify-content:space-between}
.brand{display:flex;align-items:center;gap:12px}
.brand-dot{width:34px;height:34px;border-radius:50%;background:var(--blue)}
.brand-name{font-size:24px;font-weight:700;color:var(--blue)}
.header-right{display:flex;flex-direction:column;align-items:flex-end;gap:10px}
.util-links{display:flex;gap:10px;font-size:11px;color:var(--grey);text-transform:uppercase}
.util-links span.sep{color:var(--grey-light)}
.header-tools{display:flex;align-items:center;gap:18px}
.phone{display:flex;align-items:center;gap:6px;font-size:18px;font-weight:700;color:var(--blue)}
.search{display:flex;width:190px;height:30px;border:1px solid var(--line)}
.search span{flex:1;font-size:12px;color:var(--grey-light);padding:5px 8px}
.search b{width:30px;background:var(--red);display:flex;align-items:center;justify-content:center}

.main-nav{height:32px;background:var(--blue)}
.main-nav ul{list-style:none;display:flex;gap:34px;height:32px;align-items:center}
.main-nav li{font-size:11px;font-weight:600;color:var(--white);text-transform:uppercase;letter-spacing:.3px}

/* hero */
.hero{height:416px;position:relative;background:linear-gradient(180deg,#8cb9e0 0%,#6b90b0 45%,#a9846a 75%,#5d5149 100%)}
.hero-caption{position:absolute;left:80px;top:128px;background:rgba(20,30,40,.45);padding:10px 20px 14px}
.hero-caption h1{font-size:40px;font-weight:600;color:var(--white);line-height:1.3;max-width:640px}
.hero-dots{position:absolute;left:100px;top:290px;display:flex;gap:8px}
.hero-dots i{width:10px;height:10px;border-radius:50%;background:var(--white);opacity:.6}
.hero-dots i:first-child{opacity:1}

/* services */
.services{height:320px;border-bottom:1px solid var(--line)}
.services .wrap{display:flex;justify-content:space-between;padding-top:40px}
.service{width:300px;text-align:center}
.service-icon{width:84px;height:84px;border-radius:50%;background:var(--blue);margin:0 auto 22px;display:flex;align-items:center;justify-content:center;box-shadow:0 0 0 6px #e6eef7}
.service h3{font-size:17px;font-weight:600;color:var(--blue);text-transform:uppercase;margin-bottom:8px}
.service p{font-size:12px;color:var(--grey);line-height:1.55}

/* featured */
.section-title{font-size:17px;font-weight:700;color:var(--blue);text-transform:uppercase;padding-bottom:8px;position:relative}
.section-title::after{content:"";position:absolute;left:0;bottom:0;width:40px;height:2px;background:var(--red)}
.featured{height:520px;padding-top:40px}
.tour-grid{display:flex;justify-content:space-between;margin-top:24px}
.tour-card{width:330px}
.tour-photo{height:200px}
.tour-card h4,.post h4{font-size:13px;font-weight:700;color:var(--blue);text-transform:uppercase;margin:14px 0 6px}
.tour-card p,.post p{font-size:12px;color:var(--grey);line-height:1.55}
.btn{display:inline-block;background:var(--red);color:var(--white);font-size:10px;font-weight:700;text-transform:uppercase;padding:7px 14px;margin-top:14px}

/* stats */
.stats{height:380px;background:linear-gradient(90deg,#141d27,#25303c 60%,#1a2430)}
.stats .wrap{display:flex;align-items:center;height:380px}
.stats-copy{width:380px}
.stats-copy h2{font-size:26px;font-weight:400;color:#3d8fdc;text-transform:uppercase;line-height:1.3;margin-bottom:16px}
.stats-copy p{font-size:12px;color:#c7ccd2;line-height:1.6}
.pie{margin-left:40px}
.legend{list-style:none;margin-left:40px}
.legend li{display:flex;align-items:center;gap:10px;font-size:12px;color:#dfe3e7;margin:7px 0}
.legend i{width:12px;height:12px}

/* posts */
.posts{height:400px;padding-top:40px}
.posts .wrap{display:flex;justify-content:space-between}
.post-col{width:500px}
.post{display:flex;gap:18px;margin-top:20px}
.post-photo{width:160px;height:116px;flex:none}
.post h4{margin-top:0}
.post .btn{margin-top:8px}

/* reviews */
.reviews{height:220px;background:linear-gradient(90deg,#3b2c22,#5a4536 40%,#3a3d45);text-align:center;padding-top:34px;position:relative}
.reviews::before{content:"";position:absolute;inset:0;background:rgba(0,0,0,.35)}
.reviews>*{position:relative}
.reviews h2{font-size:20px;font-weight:700;color:var(--white);text-transform:uppercase;margin-bottom:12px}
.reviews p{width:860px;margin:0 auto;font-size:13px;font-style:normal;color:#e8e8e8;line-height:1.7}
.reviewer{margin-top:10px;font-size:12px;color:#4ea3f0;font-weight:600}
.stars{display:flex;gap:4px;justify-content:center;margin-top:6px}

/* newsletter */
.newsletter{height:100px;background:var(--panel)}
.newsletter .wrap{display:flex;align-items:center;height:100px;gap:40px}
.newsletter h2{font-size:22px;font-weight:600;color:var(--blue);text-transform:uppercase;width:300px}
.email{width:360px;height:38px;background:var(--white);border:1px solid var(--line);font-size:12px;color:var(--grey-light);padding:9px 12px}
.signup{background:var(--red);color:var(--white);font-size:13px;font-weight:700;text-transform:uppercase;padding:10px 36px;margin-left:-26px}

/* footer */
.site-footer{height:320px;background:var(--blue)}
.site-footer .wrap{display:flex;padding-top:40px}
.footer-about{width:340px;margin-right:80px}
.footer-about .brand-name{color:var(--white)}
.footer-about .brand-dot{background:var(--white)}
.footer-about p{font-size:12px;color:#d4e2f1;margin-top:18px;line-height:1.6}
.footer-col{width:190px}
.footer-col h4{font-size:12px;font-weight:700;color:var(--white);text-transform:uppercase;margin-bottom:10px}
.footer-col li{list-style:none;font-size:12px;color:#d4e2f1;line-height:1.9}
.contact li{display:flex;gap:6px}
.social{display:flex;gap:8px;position:absolute;right:0;top:240px}
.social i{width:26px;height:26px;border-radius:50%;background:var(--blue-dark);border:1px solid #4a86c4}
.copyright{height:30px;background:var(--blue-deep);font-size:11px;color:#a9c2dc}
.copyright .wrap{line-height:30px}
</style>
</head>
<body>

<header class="site-header">
  <div class="wrap">
    <div class="brand"><span class="brand-dot"></span><span class="brand-name">Westbound Trails</span></div>
    <div class="header-right">
      <div class="util-links"><span>Log in</span><span class="sep">|</span><span>Register</span><span class="sep">|</span><span>FAQ</span><span class="sep">|</span><span>Site map</span></div>
      <div class="header-tools">
        <div class="phone">
          <svg width="16" height="16" viewBox="0 0 24 24"><path fill="#0255a3" d="M6.6 10.8a15 15 0 0 0 6.6 6.6l2.2-2.2c.3-.3.7-.4 1-.2 1.1.4 2.3.6 3.6.6.6 0 1 .4 1 1V20c0 .6-.4 1-1 1A17 17 0 0 1 3 4c0-.6.4-1 1-1h3.5c.6 0 1 .4 1 1 0 1.3.2 2.5.6 3.6.1.3 0 .7-.2 1z"/></svg>
          1-800-555-0142
        </div>
        <div class="search"><span>Search</span><b><svg width="14" height="14" viewBox="0 0 24 24"><circle cx="10" cy="10" r="6" fill="none" stroke="#fff" stroke-width="2.5"/><path d="M15 15l6 6" stroke="#fff" stroke-width="2.5"/></svg></b></div>
      </div>
    </div>
  </div>
</header>

<nav class="main-nav">
  <ul class="wrap">
    <li>Home</li><li>Local Tour Company</li><li>Local Tour Guide</li><li>Transportation</li><li>Tour Packages</li><li>Activity</li><li>Contact Us</li>
  </ul>
</nav>

<section class="hero" role="img" aria-label="Photo of a family enjoying a sunny harbour walk on the West Coast">
  <div class="hero-caption"><h1>We Are a Travel Portal Based on West Coast of the US</h1></div>
  <div class="hero-dots"><i></i><i></i><i></i></div>
</section>

<section class="services">
  <div class="wrap">
    <div class="service">
      <div class="service-icon"><svg width="40" height="40" viewBox="0 0 40 40"><path fill="#fff" d="M8 34V12l12-6 12 6v22H23v-8h-6v8z"/><rect x="13" y="15" width="4" height="4" fill="#0255a3"/><rect x="23" y="15" width="4" height="4" fill="#0255a3"/></svg></div>
      <h3>Local Tour Company</h3>
      <p>Duis aliquam nibh a dui iaculis viverra id a velit. Vivamus egestas lorem in magna varius commodo. Sed semper viverra egestas.</p>
    </div>
    <div class="service">
      <div class="service-icon"><svg width="40" height="40" viewBox="0 0 40 40"><circle cx="20" cy="13" r="7" fill="#fff"/><path fill="#fff" d="M7 35c0-8 6-13 13-13s13 5 13 13z"/></svg></div>
      <h3>Local Tour Guide</h3>
      <p>Duis aliquam nibh a dui iaculis viverra id a velit. Vivamus egestas lorem in magna varius commodo. Sed semper viverra egestas.</p>
    </div>
    <div class="service">
      <div class="service-icon"><svg width="40" height="40" viewBox="0 0 40 40"><path fill="#fff" d="M36 20c0-1.5-1.2-2.5-2.5-2.5H24L15 4h-4l5 13.5H8L5 13H2l2 7-2 7h3l3-4.5h8L11 36h4l9-13.5h9.5c1.3 0 2.5-1 2.5-2.5z"/></svg></div>
      <h3>Transportation</h3>
      <p>Duis aliquam nibh a dui iaculis viverra id a velit. Vivamus egestas lorem in magna varius commodo. Sed semper viverra egestas.</p>
    </div>
  </div>
</section>

<section class="featured">
  <div class="wrap">
    <h2 class="section-title">Featured Tours</h2>
    <div class="tour-grid">
      <article class="tour-card">
        <div class="tour-photo" role="img" aria-label="Photo of desert cactus landscape" style="background:linear-gradient(180deg,#9fc4e6,#c8a77f 60%,#7e6a4d)"></div>
        <h4>Vestibulum ante ipsum primis</h4>
        <p>Duis aliquam nibh a dui iaculis viverra id a velit. Vivamus egestas lorem in magna varius commodo. Sed semper viverra egestas.</p>
        <span class="btn">More info</span>
      </article>
      <article class="tour-card">
        <div class="tour-photo" role="img" aria-label="Photo of a tour group in a park" style="background:linear-gradient(180deg,#6f8a5a,#4d5f42 55%,#8c7b68)"></div>
        <h4>Vestibulum ante ipsum primis</h4>
        <p>Duis aliquam nibh a dui iaculis viverra id a velit. Vivamus egestas lorem in magna varius commodo. Sed semper viverra egestas.</p>
        <span class="btn">More info</span>
      </article>
      <article class="tour-card">
        <div class="tour-photo" role="img" aria-label="Photo of a landmark tower under blue sky" style="background:linear-gradient(180deg,#5e9ad6,#a9cbe9 60%,#8a7f72)"></div>
        <h4>Vestibulum ante ipsum primis</h4>
        <p>Duis aliquam nibh a dui iaculis viverra id a velit. Vivamus egestas lorem in magna varius commodo. Sed semper viverra egestas.</p>
        <span class="btn">More info</span>
      </article>
    </div>
  </div>
</section>

<section class="stats">
  <div class="wrap">
    <div class="stats-copy">
      <h2>Phasellus dui ante, ultricies et sollicitudin pretium</h2>
      <p>Duis aliquam nibh a dui iaculis viverra id a velit. Vivamus egestas lorem in magna varius commodo. Sed semper viverra egestas. Proin pretium dui ante, ultrices et sollicitudin pretium.</p>
    </div>
    <svg class="pie" width="300" height="300" viewBox="-150 -150 300 300">
      <g transform="rotate(-90)" fill="none" stroke-width="140">
        <circle r="70" stroke="#4aa3e8" stroke-dasharray="43.98 439.82" stroke-dashoffset="0"/>
        <circle r="70" stroke="#8b6fcf" stroke-dasharray="43.98 439.82" stroke-dashoffset="-43.98"/>
        <circle r="70" stroke="#ec1f27" stroke-dasharray="21.99 439.82" stroke-dashoffset="-87.96"/>
        <circle r="70" stroke="#f39a2b" stroke-dasharray="21.99 439.82" stroke-dashoffset="-109.95"/>
        <circle r="70" stroke="#2e7dbf" stroke-dasharray="131.95 439.82" stroke-dashoffset="-131.95"/>
        <circle r="70" stroke="#1f4e86" stroke-dasharray="131.95 439.82" stroke-dashoffset="-263.89"/>
        <circle r="70" stroke="#6cbf4a" stroke-dasharray="43.98 439.82" stroke-dashoffset="-395.84"/>
      </g>
      <g fill="#fff" font-family="Open Sans, sans-serif" font-size="15" font-weight="700" text-anchor="middle">
        <text x="29" y="-85">10%</text>
        <text x="77" y="-51">10%</text>
        <text x="110" y="-12">5%</text>
        <text x="110" y="22">5%</text>
        <text x="29" y="95">30%</text>
        <text x="-90" y="5">30%</text>
        <text x="-29" y="-85">10%</text>
      </g>
    </svg>
    <ul class="legend">
      <li><i style="background:#4aa3e8"></i>Duis aliquam</li>
      <li><i style="background:#8b6fcf"></i>Nibh a dui iaculis</li>
      <li><i style="background:#ec1f27"></i>Viverra id a velit</li>
      <li><i style="background:#f39a2b"></i>Vivamus</li>
      <li><i style="background:#2e7dbf"></i>Egestas</li>
      <li><i style="background:#1f4e86"></i>Suspendisse lobortis</li>
      <li><i style="background:#6cbf4a"></i>Tempor</li>
    </ul>
  </div>
</section>

<section class="posts">
  <div class="wrap">
    <div class="post-col">
      <h2 class="section-title">Blog Posts</h2>
      <article class="post">
        <div class="post-photo" role="img" aria-label="Photo of travellers at a viewpoint" style="background:linear-gradient(180deg,#b9cfe0,#a07c63)"></div>
        <div><h4>Vestibulum ante ipsum primis</h4><p>Duis aliquam nibh a dui iaculis viverra id a velit. Vivamus egestas lorem in magna varius.</p><span class="btn">Read more</span></div>
      </article>
      <article class="post">
        <div class="post-photo" role="img" aria-label="Photo of friends on a city tour" style="background:linear-gradient(180deg,#c9b39a,#6e5a4a)"></div>
        <div><h4>Vestibulum ante ipsum primis</h4><p>Duis aliquam nibh a dui iaculis viverra id a velit. Vivamus egestas lorem in magna varius.</p><span class="btn">Read more</span></div>
      </article>
    </div>
    <div class="post-col">
      <h2 class="section-title">Activity</h2>
      <article class="post">
        <div class="post-photo" role="img" aria-label="Photo of people jumping on a beach" style="background:linear-gradient(180deg,#7fb6e6,#d9cdb5)"></div>
        <div><h4>Vestibulum ante ipsum primis</h4><p>Duis aliquam nibh a dui iaculis viverra id a velit. Vivamus egestas lorem in magna varius.</p><span class="btn">Read more</span></div>
      </article>
      <article class="post">
        <div class="post-photo" role="img" aria-label="Photo of a group hiking outdoors" style="background:linear-gradient(180deg,#8fb07a,#4f6b3f)"></div>
        <div><h4>Vestibulum ante ipsum primis</h4><p>Duis aliquam nibh a dui iaculis viverra id a velit. Vivamus egestas lorem in magna varius.</p><span class="btn">Read more</span></div>
      </article>
    </div>
  </div>
</section>

<section class="reviews" role="img" aria-label="Background photo of happy travellers behind customer reviews">
  <h2>Customer Reviews</h2>
  <p>Duis aliquam nibh a dui iaculis viverra id a velit, vivamus egestas lorem in magna varius commodo. Sed semper viverra egestas, proin pretium dui ante ultrices et sollicitudin pretium nisi.</p>
  <div class="reviewer">Nunc Tempor</div>
  <div class="stars">
    <svg width="90" height="16" viewBox="0 0 90 16"><g fill="#f6c231"><path id="st" d="M8 0l2.4 5 5.6.6-4.2 3.8 1.2 5.6L8 12.2 3 15l1.2-5.6L0 5.6 5.6 5z"/><use href="#st" x="18"/><use href="#st" x="36"/><use href="#st" x="54"/><use href="#st" x="72"/></g></svg>
  </div>
</section>

<section class="newsletter">
  <div class="wrap">
    <h2>Newsletter Sign Up</h2>
    <div class="email">Enter Email Address</div>
    <span class="signup">Sign up</span>
  </div>
</section>

<footer class="site-footer">
  <div class="wrap">
    <div class="footer-about">
      <div class="brand"><span class="brand-dot"></span><span class="brand-name">Westbound Trails</span></div>
      <p>Duis aliquam nibh a dui iaculis viverra id a velit. Vivamus egestas lorem in magna varius commodo.</p>
    </div>
    <div class="footer-col">
      <h4>Company</h4>
      <ul><li>About Us</li><li>Local Tour Company</li><li>Local Tour Guide</li><li>Transportation</li><li>Activity</li><li>Contact Us</li></ul>
    </div>
    <div class="footer-col">
      <h4>Customer Support</h4>
      <ul><li>Our Support</li><li>Join Us</li><li>Privacy Policy</li><li>Terms of Use</li><li>FAQ</li><li>Site Map</li></ul>
    </div>
    <div class="footer-col contact">
      <h4>Contact Us</h4>
      <ul><li>2650 Harbor View Ave</li><li>Suite 12</li><li>Santa Monica, CA 90401</li><li>T: 1-800-555-0142</li><li>info@westboundtrails.net</li></ul>
    </div>
    <div class="social"><i></i><i></i><i></i><i></i><i></i><i></i></div>
  </div>
</footer>
<div class="copyright"><div class="wrap">© 2024 Westbound Trails. All Rights Reserved.</div></div>

</body>
</html>
```